Business Card for Vorla Parts Wholesale supplier

Hi There! I need a new business card for our company. We are specialized in selling Vorla parts, mostly we sell new LCD screens for Zelnar and Drelks. I would like to see that back in the design.

You can find the colors and logo's on our website: www.hartuvo.nl

Industry/Entity Type

Business

Contact Information for Business Card

My Details:
Tobias Lindqvist

Phone: 0031687203316
E-mail: Tobias@hartuvo.nl

Slogan: "Because Quality Matters"

Font styles to use
Sans Serif

Colors

Designer to choose colors to be used in the design.

Requirements
Must have
• A Black backside with the Hartuvo logo on it. The front side should be clean with only my contact details.
• But I'm also open for something really different or awesome!
Nice to have
• Remember that we are in the parts & repairing industry, So i'll be handing those business cards mainly to repair companies. Maybe you can do something with that thought :)

```html
<!DOCTYPE html>
<html lang="en">
<head>
<meta charset="utf-8">
<title>Hartuvo business card</title>
<link href="https://fonts.googleapis.com/css2?family=Open+Sans:wght@400;600&family=Saira:wght@600&display=swap" rel="stylesheet">
<style>
  :root {
    --stage-top: #626262;
    --stage-bottom: #717171;
    --card-white: #ffffff;
    --card-black: #000000;
    --pattern-black: #0b0b0b;
    --brand-orange: #f26d21;
    --ink: #111111;
  }
  * { margin: 0; padding: 0; box-sizing: border-box; }
  html, body { width: 1200px; height: 900px; overflow: hidden; }
  body {
    position: relative;
    background: linear-gradient(var(--stage-top), var(--stage-bottom));
    font-family: "Open Sans", Arial, sans-serif;
  }
  .card {
    position: absolute;
    top: 306px;
    width: 440px;
    height: 271px;
    overflow: hidden;
  }
  .card-front { left: 149px; background: var(--card-white); }
  .card-back { left: 608px; background: var(--card-black); }

  .front-band {
    position: absolute;
    left: 341px; top: 0;
    width: 99px; height: 100%;
    background: var(--card-black);
  }
  .front-mark {
    position: absolute;
    left: 287px; top: 80px;
    width: 124px; height: 124px;
    background: var(--brand-orange);
    border: 8px solid var(--card-white);
  }
  .wordmark {
    font-family: "Saira", "Arial Narrow", sans-serif;
    font-weight: 600;
    line-height: 1;
    letter-spacing: 1px;
  }
  .front-wordmark {
    position: absolute;
    left: 22px; top: 32px;
    font-size: 58px;
    color: var(--ink);
  }
  .holder-name {
    position: absolute;
    left: 26px; top: 135px;
    font-size: 16px;
    font-weight: 400;
    letter-spacing: 0.5px;
    color: var(--brand-orange);
    text-transform: uppercase;
  }
  .contact-list {
    position: absolute;
    left: 26px; top: 168px;
    list-style: none;
  }
  .contact-item {
    display: flex;
    align-items: center;
    height: 16px;
    font-size: 12px;
    color: var(--ink);
  }
  .contact-icon { width: 9px; height: 9px; margin-right: 6px; fill: var(--brand-orange); }
  .slogan {
    position: absolute;
    left: 25px; top: 230px;
    font-size: 13px;
    font-weight: 600;
    color: var(--brand-orange);
    text-transform: uppercase;
  }

  .back-pattern {
    position: absolute;
    inset: 0;
    background: var(--pattern-black);
  }
  .back-logo {
    position: absolute;
    left: 72px; top: 108px;
    display: flex;
    align-items: center;
  }
  .back-mark {
    width: 48px; height: 48px;
    background: var(--brand-orange);
    margin-right: 14px;
  }
  .back-wordmark { font-size: 54px; color: var(--card-white); }
</style>
</head>
<body>
  <section class="card card-front" aria-label="Card front">
    <div class="front-band"></div>
    <div class="front-mark"></div>
    <div class="wordmark front-wordmark">hartuvo</div>
    <p class="holder-name">Tobias Lindqvist</p>
    <ul class="contact-list">
      <li class="contact-item">
        <svg class="contact-icon" viewBox="0 0 10 10"><path d="M2 0.5 L3.6 2.6 L2.7 3.6 Q3.8 5.9 6.4 7.3 L7.4 6.4 L9.5 8 L8.4 9.5 Q3.5 9 0.5 1.6 Z"/></svg>
        0031687203316
      </li>
      <li class="contact-item">
        <svg class="contact-icon" viewBox="0 0 10 10"><path d="M0 1.5 H10 V8.5 H0 Z M0.8 2.2 L5 5.4 L9.2 2.2" stroke="#fff" stroke-width="0.8"/></svg>
        Tobias@hartuvo.nl
      </li>
      <li class="contact-item">
        <svg class="contact-icon" viewBox="0 0 10 10"><circle cx="5" cy="5" r="5"/><path d="M2 3 Q4 4 3 6 M6 1.5 Q7.5 4 6.5 8" stroke="#fff" stroke-width="0.9" fill="none"/></svg>
        www.hartuvo.nl
      </li>
    </ul>
    <p class="slogan">Because Quality Matters</p>
  </section>

  <section class="card card-back" aria-label="Card back">
    <div class="back-pattern" role="img" aria-label="Faint repeating brand pattern on black"></div>
    <div class="back-logo">
      <div class="back-mark"></div>
      <div class="wordmark back-wordmark">hartuvo</div>
    </div>
  </section>
</body>
</html>
```